High-end construction company needs a business card design

We need a modern looking business card that draws people in, is memorable and looks so good people will want to sick it on their fridges.
On the first side what is needed are:
Logo
My name - Tomasz Brelwik
Title - Managing Director
Website - www.varkelt.co.uk
Email - tomasz@varkelt.co.uk
Telephone - 020 5194 6281
Mobile - 07845139072
On the back side was is needed is a list of all the services we provide:
-Kitchen Renovations
-Bathroom Renovations
-House Renovations
-Garage Conversions
-Extensions
-Loft Conversions
-Conservatories
-Carpentry
-Tiling
-Electrical
-Plumbing & Heating
-Bricklaying
-Landscaping
-Decorating
-Plastering
We would like the colours to be the same shades as on the logo with grey or black for the words.
Target Market(s)
Anyone who needs building work done
Contact Information for Business Card
This business card is for a construction company which strives to deliver excellent service and quality.
The look and feel of the card should represent this.
Requirements
Must have
- On the first side what is needed are:
Logo
My name - Tomasz Brelwik
Title - Managing Director
Website - www.varkelt.co.uk
Email - tomasz@varkelt.co.uk
Telephone - 020 5194 6281
Mobile - 07845139072
Nice to have
- Cool looking features

```html
<!DOCTYPE html>
<html lang="en">
<head>
<meta charset="utf-8">
<title>Varkelt Construction Ltd – Business Card</title>
<link rel="stylesheet" href="https://fonts.googleapis.com/css2?family=Archivo+Black&family=Arimo:wght@400;700&display=swap">
<style>
  :root {
    --bg: #c9c9c9;
    --green-light: #78c043;
    --green-dark: #4a8f3f;
    --green-brand: #5cb135;
    --ink: #2a2a2a;
    --white: #ffffff;
    --faint: #eef6ea;
  }
  * { margin: 0; padding: 0; box-sizing: border-box; }
  html, body { width: 1200px; height: 900px; overflow: hidden; }
  body {
    background: var(--bg);
    font-family: "Arimo", Arial, sans-serif;
    position: relative;
  }
  .card {
    position: absolute;
    width: 700px;
    height: 400px;
    border-radius: 30px;
    overflow: hidden;
    box-shadow: 0 6px 16px rgba(0,0,0,0.25);
  }
  /* Back: services */
  .card--back {
    left: 80px; top: 40px;
    background: linear-gradient(200deg, var(--green-light) 0%, var(--green-dark) 100%);
    color: var(--white);
  }
  .services {
    position: absolute;
    list-style: none;
    font-size: 17px;
    letter-spacing: 0.04em;
    text-transform: uppercase;
    line-height: 30px;
  }
  .services li::before {
    content: "";
    display: inline-block;
    width: 9px; height: 9px;
    border-radius: 50%;
    background: var(--white);
    margin-right: 14px;
    vertical-align: middle;
    position: relative; top: -2px;
  }
  .services--main { left: 70px; top: 110px; }
  .services--trades { left: 400px; top: 70px; }

  /* Front: contact */
  .card--front {
    left: 420px; top: 460px;
    background: var(--white);
    color: var(--ink);
  }
  .decor-motif {
    position: absolute;
    left: 400px; top: 30px;
    width: 270px; height: 210px;
    border-radius: 20px;
    background: radial-gradient(ellipse at center, var(--faint) 0%, rgba(238,246,234,0) 72%);
  }
  .brand {
    position: absolute;
    left: 60px; top: 70px;
    font-family: "Archivo Black", "Arial Black", sans-serif;
    color: var(--green-brand);
  }
  .brand__name { font-size: 62px; line-height: 1; letter-spacing: 0.02em; }
  .brand__suffix { font-size: 20px; letter-spacing: 0.12em; margin-top: 6px; }
  .person {
    position: absolute;
    left: 60px; top: 212px;
  }
  .person__name {
    font-family: "Archivo Black", "Arial Black", sans-serif;
    color: var(--green-brand);
    font-size: 26px;
    text-transform: uppercase;
    letter-spacing: 0.02em;
  }
  .person__title { font-size: 20px; margin-top: 2px; }
  .phones {
    position: absolute;
    left: 60px; top: 300px;
    list-style: none;
    font-size: 21px;
    line-height: 30px;
  }
  .phones li, .online li { display: flex; align-items: center; gap: 10px; }
  .icon { width: 18px; height: 18px; flex: none; }
  .online {
    position: absolute;
    right: 40px; top: 262px;
    list-style: none;
    font-size: 18px;
    line-height: 28px;
    text-align: right;
  }
  .online li { justify-content: flex-end; }
</style>
</head>
<body>

<section class="card card--back" aria-label="Services">
  <ul class="services services--main">
    <li>Kitchen Renovations</li>
    <li>Bathroom Renovations</li>
    <li>House Renovations</li>
    <li>Garage Conversions</li>
    <li>Extensions</li>
    <li>Loft Conversions</li>
    <li>Conservatories</li>
    <li>Carpentry</li>
  </ul>
  <ul class="services services--trades">
    <li>Tiling</li>
    <li>Electrical</li>
    <li>Plumbing &amp; Heating</li>
    <li>Bricklaying</li>
    <li>Landscaping</li>
    <li>Decorating</li>
    <li>Plastering</li>
  </ul>
</section>

<section class="card card--front" aria-label="Contact details">
  <div class="decor-motif" role="img" aria-label="Faint brand motif decoration"></div>

  <div class="brand">
    <div class="brand__name">VARKELT</div>
    <div class="brand__suffix">CONSTRUCTION LTD</div>
  </div>

  <div class="person">
    <div class="person__name">Tomasz Brelwik</div>
    <div class="person__title">Managing Director</div>
  </div>

  <ul class="phones">
    <li>
      <svg class="icon" viewBox="0 0 24 24" aria-hidden="true"><path fill="var(--green-brand)" d="M6.6 10.8a15 15 0 0 0 6.6 6.6l2.2-2.2a1 1 0 0 1 1-.25 11.4 11.4 0 0 0 3.6.57 1 1 0 0 1 1 1V20a1 1 0 0 1-1 1A17 17 0 0 1 3 4a1 1 0 0 1 1-1h3.5a1 1 0 0 1 1 1c0 1.25.2 2.45.57 3.57a1 1 0 0 1-.25 1z"/></svg>
      020 5194 6281
    </li>
    <li>
      <svg class="icon" viewBox="0 0 24 24" aria-hidden="true"><rect x="6" y="2" width="12" height="20" rx="2" fill="none" stroke="var(--green-brand)" stroke-width="2.2"/><circle cx="12" cy="18" r="1.2" fill="var(--green-brand)"/></svg>
      07845139072
    </li>
  </ul>

  <ul class="online">
    <li>
      tomasz@varkelt.co.uk
      <svg class="icon" viewBox="0 0 24 24" aria-hidden="true"><rect x="2" y="5" width="20" height="14" rx="1.5" fill="var(--green-brand)"/><path d="M3 6l9 7 9-7" fill="none" stroke="#fff" stroke-width="1.8"/></svg>
    </li>
    <li>
      www.varkelt.co.uk
      <svg class="icon" viewBox="0 0 24 24" aria-hidden="true"><circle cx="12" cy="12" r="10" fill="var(--green-brand)"/><path d="M2 12h20M12 2c3 3 3 17 0 20M12 2c-3 3-3 17 0 20" fill="none" stroke="#fff" stroke-width="1.4"/></svg>
    </li>
  </ul>
</section>

</body>
</html>
```